KRV Business Card

Looking for a business card for my restaurant group I own. Four different concepts:

Copperfield Alehouse
Bristow Alehouse
Tanager's Stone Hearth Kitchen
Pellston Patty Company

Card doesn't need to include all the logos.

```html
<!DOCTYPE html>
<html lang="en">
<head>
<meta charset="utf-8">
<title>KRV Business Card</title>
<link href="https://fonts.googleapis.com/css2?family=Montserrat:wght@600;700&family=Open+Sans:wght@400;700&display=swap" rel="stylesheet">
<style>
  :root {
    --stage: #3a3b3d;
    --card: #141414;
    --gold: #d8b56a;
    --grey: #6f7073;
    --rule: #4a4a4a;
    --text: #f2f2f2;
  }
  * { box-sizing: border-box; margin: 0; padding: 0; }
  html, body { width: 1200px; height: 900px; overflow: hidden; }
  body {
    background: var(--stage);
    font-family: "Open Sans", sans-serif;
    position: relative;
  }
  .card {
    position: absolute;
    width: 540px;
    height: 309px;
    background: var(--card);
    border-radius: 26px;
    overflow: hidden;
    box-shadow: 0 18px 40px rgba(0,0,0,.45);
  }
  .card--front { left: 40px; top: 296px; }
  .card--back  { left: 620px; top: 296px; }

  .band { position: absolute; bottom: 0; height: 11px; }
  .card--front .band { left: 0; right: 0; background: var(--gold); }
  .band--gold { left: 0; width: 76%; background: var(--gold); }
  .band--grey { right: 0; width: 23%; background: var(--grey); }

  .brand {
    display: flex;
    align-items: center;
    gap: 10px;
    font-family: "Montserrat", sans-serif;
    font-weight: 700;
    color: var(--gold);
    letter-spacing: 2px;
    text-transform: uppercase;
    line-height: 1.15;
  }
  .brand__mark { width: 14px; height: 14px; background: var(--gold); flex: none; }
  .card--front .brand {
    position: absolute; left: 0; right: 0; top: 118px;
    justify-content: center; font-size: 26px;
  }
  .card--back .brand {
    position: absolute; right: 34px; top: 42px;
    font-size: 17px; text-align: right;
  }

  .divider { position: absolute; height: 1px; background: var(--rule); }
  .divider--long { left: 168px; right: 30px; top: 186px; }
  .divider--short { left: 40px; width: 128px; top: 214px; }

  .person { position: absolute; left: 40px; top: 150px; }
  .person__name { color: var(--gold); font-weight: 700; font-size: 19px; line-height: 1.2; }
  .person__company { color: var(--text); font-size: 14px; margin-top: 4px; }

  .contacts { position: absolute; left: 48px; top: 228px; list-style: none; }
  .contacts li {
    display: flex; align-items: center; gap: 10px;
    color: var(--text); font-size: 14px; line-height: 21px;
  }
  .contacts svg { width: 12px; height: 12px; flex: none; }
</style>
</head>
<body>

<section class="card card--front" aria-label="Card front">
  <div class="brand"><span class="brand__mark"></span>Kestrel Ridge Hospitality</div>
  <div class="band"></div>
</section>

<section class="card card--back" aria-label="Card back">
  <div class="brand"><span class="brand__mark"></span>Kestrel Ridge<br>Hospitality</div>

  <div class="person">
    <p class="person__name">Dana Voskuil</p>
    <p class="person__company">Kestrel Ridge Hospitality</p>
  </div>
  <div class="divider divider--long"></div>
  <div class="divider divider--short"></div>

  <ul class="contacts">
    <li>
      <svg viewBox="0 0 24 24" fill="var(--gold)"><path d="M6.6 10.8a15.1 15.1 0 0 0 6.6 6.6l2.2-2.2a1 1 0 0 1 1-.25 11.4 11.4 0 0 0 3.6.57 1 1 0 0 1 1 1V20a1 1 0 0 1-1 1A17 17 0 0 1 3 4a1 1 0 0 1 1-1h3.5a1 1 0 0 1 1 1c0 1.25.2 2.45.57 3.57a1 1 0 0 1-.25 1z"/></svg>
      555-014-2290
    </li>
    <li>
      <svg viewBox="0 0 24 24" fill="none" stroke="var(--gold)" stroke-width="2.4"><rect x="2" y="5" width="20" height="14" rx="1"/><path d="M2 6l10 7 10-7"/></svg>
      dana@krvkitchens.com
    </li>
    <li>
      <svg viewBox="0 0 24 24" fill="none" stroke="var(--gold)" stroke-width="2.2"><circle cx="12" cy="12" r="10"/><path d="M2 12h20M12 2c3 3 3 17 0 20M12 2c-3 3-3 17 0 20"/></svg>
      www.krvkitchens.com
    </li>
  </ul>

  <div class="band band--gold"></div>
  <div class="band band--grey"></div>
</section>

</body>
</html>
```